Vegetable Grower Expo Backdrop

I need an 8x8 backdrop for an expo booth. We are a vegetable grower and have very limited graphics to work with. I have uploaded our logo which may not be the correct format and need to be updated for quality to print at that size. Need something quick and simple. Expo is August 18th

Target Market(s)

Retail and Wholesale buyers

Industry/Entity Type

Produce

Colors

Designer to choose colors to be used in the design.

Requirements
Must have
• Logo
Nice to have
• I am open to ideas!
Should not have
• Keep it simple and bottom 1/4 will be covered with samples so focus on top 3/4 of banner

```html
<!DOCTYPE html>
<html lang="en">
<head>
<meta charset="utf-8">
<title>Vegetable Grower Expo Backdrop</title>
<link rel="stylesheet" href="https://fonts.googleapis.com/css2?family=Oswald:wght@500;700&family=Young+Serif&display=swap">
<style>
  :root {
    --canvas-grey: #c9c9c9;
    --paper: #f1f1ef;
    --paper-shade: #e4e4e2;
    --leaf-green: #5e9a3e;
    --soil-brown: #6a5322;
    --ink: #2a2a2a;
    --pill-dark: #1d7436;
    --pill-light: #46b74b;
    --divider: #2f7a3c;
  }
  * { margin: 0; padding: 0; box-sizing: border-box; }
  html, body { width: 1200px; height: 1146px; overflow: hidden; background: var(--canvas-grey); }
  .backdrop {
    position: absolute; left: 148px; top: 130px; width: 893px; height: 893px;
    background: radial-gradient(ellipse at 50% 50%, #f7f7f5 0%, var(--paper) 55%, var(--paper-shade) 100%);
    overflow: hidden;
  }
  .produce { position: absolute; }
  .produce--left {
    left: 0; top: 0; width: 205px; height: 470px;
    background: linear-gradient(160deg, #c8c96a 0%, #8da63b 35%, #3f7d2c 70%, #2c6424 100%);
    border-radius: 0 90px 140px 0;
  }
  .produce--bowl {
    left: 165px; top: 0; width: 176px; height: 105px;
    background: linear-gradient(160deg, #3b5e2a, #24421c);
    border-radius: 0 0 80px 80px;
  }
  .produce--garlic {
    left: 182px; top: 111px; width: 133px; height: 133px;
    background: radial-gradient(circle at 50% 45%, #c7b89a 0%, #ece6dc 45%, #faf8f4 100%);
    border-radius: 50%;
  }
  .produce--tomatoes {
    left: 329px; top: 0; width: 250px; height: 145px;
    background: linear-gradient(90deg, #b8251f 0%, #d9302a 45%, #c92c25 100%);
    border-radius: 0 0 90px 110px;
  }
  .produce--pepper {
    left: 573px; top: 0; width: 320px; height: 262px;
    background: linear-gradient(170deg, #f7bb22 0%, #f2a812 60%, #e79c10 100%);
    border-radius: 0 0 0 130px;
  }
  .produce--cloves {
    left: 665px; top: 250px; width: 140px; height: 135px;
    background: radial-gradient(circle at 50% 50%, #c9ae86 0%, #e9dcc8 55%, #f4eee4 100%);
    border-radius: 50%;
  }
  .produce--pear {
    left: 790px; top: 220px; width: 103px; height: 250px;
    background: linear-gradient(170deg, #7aa33a 0%, #b9c24a 45%, #cfcf62 100%);
    border-radius: 60px 0 0 70px;
  }
  .produce--lime {
    left: 851px; top: 469px; width: 84px; height: 104px;
    background: radial-gradient(circle at 60% 50%, #eef0b8, #d6df8a);
    border-radius: 50%;
  }
  .produce--bottom-left {
    left: 0; top: 803px; width: 167px; height: 90px;
    background: linear-gradient(120deg, #3d7a2c, #2a5f22);
    border-radius: 0 90px 0 0;
  }
  .produce--bottom-tomatoes {
    left: 579px; top: 862px; width: 200px; height: 31px;
    background: linear-gradient(90deg, #d9302a, #e14435);
    border-radius: 30px 30px 0 0;
  }
  .produce--bottom-garlic {
    left: 817px; top: 765px; width: 76px; height: 128px;
    background: radial-gradient(circle at 80% 50%, #c7b89a 0%, #ece6dc 50%, #faf8f4 100%);
    border-radius: 60px 0 0 60px;
  }
  .brand {
    position: absolute; left: 0; right: 0; top: 232px; text-align: center;
    font-family: "Oswald", sans-serif; font-weight: 700; color: var(--ink);
    font-size: 48px; line-height: 1.08; letter-spacing: 1px; text-transform: uppercase;
  }
  .headline {
    position: absolute; left: 0; right: 0; text-align: center;
    font-family: "Oswald", sans-serif; font-weight: 700; text-transform: uppercase; line-height: 1;
  }
  .headline span { display: inline-block; }
  .headline--top { top: 390px; font-size: 90px; color: var(--leaf-green); }
  .headline--top span { transform: scaleX(.8); }
  .headline--bottom { top: 487px; font-size: 92px; color: var(--soil-brown); }
  .headline--bottom span { transform: scaleX(.74); }
  .date-pill {
    position: absolute; left: 294px; top: 605px; width: 308px; height: 74px;
    border-radius: 4px 22px 4px 22px;
    background: linear-gradient(90deg, var(--pill-dark), var(--pill-light));
    color: #fff; font-family: "Oswald", sans-serif; font-weight: 500;
    font-size: 48px; line-height: 72px; text-align: center;
  }
  .highlight {
    position: absolute; top: 700px; white-space: nowrap;
    font-family: "Young Serif", serif; font-size: 22px; line-height: 29px; color: var(--ink);
  }
  .highlight--one { left: 82px; }
  .highlight--two { left: 348px; }
  .highlight--three { left: 582px; }
  .divider { position: absolute; top: 700px; width: 20px; height: 56px; }
  .divider--one { left: 308px; }
  .divider--two { left: 544px; }
</style>
</head>
<body>
  <main class="backdrop">
    <div class="produce produce--left" role="img" aria-label="Halved avocado, sliced zucchini and fresh parsley"></div>
    <div class="produce produce--bowl" role="img" aria-label="Bowl of seaweed salad"></div>
    <div class="produce produce--garlic" role="img" aria-label="Whole garlic bulb"></div>
    <div class="produce produce--tomatoes" role="img" aria-label="Red chillies and vine cherry tomatoes"></div>
    <div class="produce produce--pepper" role="img" aria-label="Yellow bell pepper"></div>
    <div class="produce produce--cloves" role="img" aria-label="Garlic cloves"></div>
    <div class="produce produce--pear" role="img" aria-label="Pear, apple and brussels sprouts"></div>
    <div class="produce produce--lime" role="img" aria-label="Lime half"></div>
    <div class="produce produce--bottom-left" role="img" aria-label="Parsley sprigs"></div>
    <div class="produce produce--bottom-tomatoes" role="img" aria-label="Cherry tomatoes and chilli"></div>
    <div class="produce produce--bottom-garlic" role="img" aria-label="Garlic bulb"></div>

    <div class="brand">Ridgeline<br>Growers</div>

    <h1 class="headline headline--top"><span>Vegetable</span></h1>
    <h2 class="headline headline--bottom"><span>Grower Expo</span></h2>

    <div class="date-pill">AUGUST 18TH</div>

    <p class="highlight highlight--one">Fresh Organic &amp;<br>Hybrid Vegetables</p>
    <svg class="divider divider--one" viewBox="0 0 20 56" aria-hidden="true">
      <line x1="10" y1="0" x2="10" y2="56" stroke="var(--divider)" stroke-width="1.5"/>
      <circle cx="10" cy="28" r="8" fill="var(--divider)"/>
      <path d="M6.5 28.2l2.4 2.4 4.6-4.8" fill="none" stroke="#fff" stroke-width="1.6" stroke-linecap="round" stroke-linejoin="round"/>
    </svg>
    <p class="highlight highlight--two">Farm-to-Table<br>Success Stories</p>
    <svg class="divider divider--two" viewBox="0 0 20 56" aria-hidden="true">
      <line x1="10" y1="0" x2="10" y2="56" stroke="var(--divider)" stroke-width="1.5"/>
      <circle cx="10" cy="28" r="8" fill="var(--divider)"/>
      <path d="M6.5 28.2l2.4 2.4 4.6-4.8" fill="none" stroke="#fff" stroke-width="1.6" stroke-linecap="round" stroke-linejoin="round"/>
    </svg>
    <p class="highlight highlight--three">Sustainable Farming<br>&amp; Agri-Tech</p>
  </main>
</body>
</html>
```